Business Cards Design for the electrical wholesaler: clean bold dynamic :)

We need a business card design that would follow our latest brand guidelines. As an electrical wholesaler we want to bring a fresh look and feel into the industry. The design should be clean bold and dynamic. It should come alive with the renewed energy of our green colour. Our grey colour should keep things balanced and complement the notion of maturity and responsibility. We employ Lato as a corporate font however are not bound by this font and we’re open to interpretation here.

Target Market(s)

Electrical contractors

Industry/Entity Type

Business

Contact Information for Business Card

Logo
Name & Surname: Halyna Dorosh
Job Title: Director of Marketing
Email: halya.dorosh@quillmail.example
Cell phone: XXX.XXX.XXXX
Address: 20517 - 87 Ave. Edmonton, AB, Canada. T6K 4N8
Business Phone: 780.555.0184
Website: www.brovix.example

Font styles to use
Other font styles liked:
• Lato

Requirements
Must have
• Logo & website
Nice to have
• Brand elements - some of them you may find in the attached Brand Guidelines (e.g. three lines on the background signifying "W")

```html
<!DOCTYPE html>
<html lang="en">
<head>
<meta charset="utf-8">
<title>Brovix Business Cards</title>
<link href="https://fonts.googleapis.com/css2?family=Lato:wght@400;700&family=Oswald:wght@500&display=swap" rel="stylesheet">
<style>
  :root {
    --backdrop: #4a443d;
    --card: #1e1e1e;
    --card-light: #2a2a2a;
    --green: #7ccc2f;
    --white: #ffffff;
    --grey: #cfcfcf;
  }
  html, body {
    margin: 0;
    padding: 0;
    width: 1200px;
    height: 930px;
    overflow: hidden;
    background: var(--backdrop);
  }
  .canvas {
    position: relative;
    width: 1200px;
    height: 930px;
  }
  .card {
    position: absolute;
    width: 520px;
    height: 297px;
    border-radius: 12px;
    background: radial-gradient(ellipse at 60% 30%, var(--card-light), var(--card) 70%);
    border-bottom: 5px solid var(--green);
    box-sizing: border-box;
    overflow: hidden;
    font-family: "Lato", sans-serif;
    color: var(--white);
  }
  .card--front { left: 70px; top: 110px; }
  .card--back { left: 610px; top: 520px; }

  .brand {
    position: absolute;
    left: 0; right: 0; top: 0; bottom: 0;
    display: flex;
    align-items: center;
    justify-content: center;
    gap: 16px;
  }
  .brand__square {
    width: 40px;
    height: 40px;
    background: var(--green);
  }
  .brand__name {
    font-size: 58px;
    font-weight: 400;
    letter-spacing: 1px;
    color: var(--white);
  }

  .person {
    position: absolute;
    left: 40px;
    top: 100px;
    width: 210px;
    text-align: right;
  }
  .person__name {
    font-family: "Oswald", sans-serif;
    font-weight: 500;
    font-size: 30px;
    line-height: 1;
    color: var(--green);
    text-transform: uppercase;
    letter-spacing: 0.5px;
  }
  .person__title {
    margin-top: 6px;
    font-size: 15px;
    color: var(--white);
  }
  .divider {
    position: absolute;
    left: 268px;
    top: 96px;
    width: 2px;
    height: 62px;
    background: var(--green);
  }
  .contact {
    position: absolute;
    left: 288px;
    top: 96px;
    margin: 0;
    padding: 0;
    list-style: none;
    font-size: 12.5px;
    line-height: 21px;
  }
  .contact li {
    display: flex;
    align-items: center;
    gap: 8px;
    white-space: nowrap;
  }
  .contact svg { width: 11px; height: 11px; flex: none; }
  .contact .accent { color: var(--green); }
  .address {
    position: absolute;
    left: 0; right: 0;
    bottom: 22px;
    text-align: center;
    font-size: 12.5px;
    color: var(--white);
  }
</style>
</head>
<body>
<main class="canvas">
  <section class="card card--front" aria-label="Card front">
    <div class="brand">
      <span class="brand__square"></span>
      <span class="brand__name">brovix</span>
    </div>
  </section>

  <section class="card card--back" aria-label="Card back">
    <div class="person">
      <div class="person__name">Halyna Dorosh</div>
      <div class="person__title">Director of Marketing</div>
    </div>
    <div class="divider"></div>
    <ul class="contact">
      <li>
        <svg viewBox="0 0 12 12" aria-hidden="true"><path d="M2.5 1l2 2-1 1.3a6 6 0 0 0 4.2 4.2L9 7.5l2 2-1.4 1.5C5.5 11 1 6.5 1 2.4z" fill="var(--green)"/></svg>
        XXX.XXX.XXXX
      </li>
      <li>
        <svg viewBox="0 0 12 12" aria-hidden="true"><rect x="1" y="2.5" width="10" height="7" fill="none" stroke="var(--green)" stroke-width="1.2"/><path d="M1 2.5l5 4 5-4" fill="none" stroke="var(--green)" stroke-width="1.2"/></svg>
        halya.dorosh@quillmail.example
      </li>
      <li>
        <svg viewBox="0 0 12 12" aria-hidden="true"><circle cx="6" cy="6" r="5" fill="none" stroke="var(--green)" stroke-width="1.2"/><path d="M1 6h10M6 1c-2.5 3-2.5 7 0 10M6 1c2.5 3 2.5 7 0 10" fill="none" stroke="var(--green)" stroke-width="1"/></svg>
        <span>www.<span class="accent">brovix</span>.example</span>
      </li>
    </ul>
    <p class="address">20517 - 87 Ave. Edmonton, AB, Canada. T6K 4N8 | Phn: 780.555.0184</p>
  </section>
</main>
</body>
</html>
```